Web Site Design For Real Estate Sales Project

The idea behind this project is pretty simple. I am putting my penthouse apartment up for sale and am trying to be creative in selling it.
Technically this will be pretty simple, it will be 3 pages but graphically this has to be as impressive as possible which is why I am trying Pixel Harbor.
The apartment is located in Barra Da Tijuca, Rio De Janeiro, Brazil. (This is where the 2016 Solstice Meet will be held)
I am looking for an index page and 2 sub-pages. I am open to all kinds of designs and navigation's but it has to make an impression quickly with a professional and enticing design. The index page should make it obvious that there is a penthouse apartment for sale in Barra Da Tijuca ( suburb of Rio De Janeiro). The first sub page is about the Condominium where the apartment is located, the second sub page is about the apartment itself.
Here is a more detailed description of what the 3 pages should be about.
Index Page
This is the landing page and should make it obvious that there is an apartment for sale in Barra Da Tijuca, Rio De Janeiro with the following attributes
251 SQ M
Duplex Penthouse
4 suites
Price R$ 2.200.000
Price per SQ M: R$ 8.764
First Sub-Page
This is about the Condominium which is called "Tranquil Cliff Suites" with the following bullets
*Family friendly and safe
*Direct access to the beach
*Many amenities like pool, football court, gym, sauna
There should be some photos of the condominium and a link to the site of the condominium ( www.tcsqv.com )
Second Sub-page
This is about the apartment. It should list in bullets the features of the apartment and then have a photo gallery of the view and various rooms. I have attached sample photos but will eventually have to use more photos.
Apartment Features
Price: R$ 2.220.000
251 m2 Duplex Penthouse
4 suites
maids room with bath
guest bathroom
living room
dinning room
Terrace with heated pool for year round use
Veranda
As mentioned above I am open to all designs and navigation so feel free to be creative. The important thing is catch peoples attention and get the message across in a few seconds, which is that there is an apartment for sale at this price with these features in this location. I will then use zintra clickreach and SEO to get people to the site.
Thanks
Men and Women from 30-60 years of age.
Apartment

```html
<!DOCTYPE html>
<html lang="en">
<head>
<meta charset="utf-8">
<title>SkydeckRio.com – Duplex Penthouse for Sale in Barra da Tijuca</title>
<link href="https://fonts.googleapis.com/css2?family=Oswald:wght@400;500&family=Arimo:wght@400&display=swap" rel="stylesheet">
<style>
:root{
  --gold:#f7c51e;
  --white:#ffffff;
  --blue:#1c6aa8;
  --text:#555555;
  --header-bg:rgba(30,38,48,.78);
  --panel:#e9e9e9;
  --page:#f1f1f1;
  --button:#666666;
  --footer:#111111;
  --footer-text:#b5b5b5;
  --dot:#ffffff;
  --dot-active:#1e8fd6;
}
*{margin:0;padding:0;box-sizing:border-box}
html,body{width:1200px;height:1101px;overflow:hidden}
body{position:relative;background:linear-gradient(#fafafa,var(--page) 30%,#ebebeb);font-family:Arimo,Arial,sans-serif;color:var(--text)}
.abs{position:absolute}
.hero-scene{left:0;top:0;width:1200px;height:678px;
  background:linear-gradient(180deg,#b9cad8 0%,#d8e2ea 12%,#5f85a8 26%,#2e5f8c 42%,#4f6a6e 58%,#5f6b55 72%,#3c4a2c 88%,#1d2414 100%)}
.site-header{left:0;top:0;width:1200px;height:68px;background:var(--header-bg);border-bottom:1px solid rgba(255,255,255,.12)}
.brand{left:131px;top:15px;font-family:Oswald,sans-serif;font-weight:500;font-size:30px;line-height:36px;color:var(--gold);letter-spacing:.3px}
.main-nav{top:24px;left:0;width:1200px;height:24px}
.main-nav a{position:absolute;font-family:Oswald,sans-serif;font-weight:500;font-size:17px;line-height:24px;color:var(--white);text-decoration:none;text-transform:uppercase}
.main-nav a.current{color:var(--gold)}
.slide{background:#fff;padding:4px;box-shadow:0 4px 14px rgba(0,0,0,.45)}
.slide .photo{width:100%;height:100%}
.slide-side{top:221px;width:220px;height:221px}
.slide-left{left:132px}
.slide-right{left:850px}
.slide-main{left:339px;top:139px;width:511px;height:316px;padding:5px;z-index:2}
.pager{top:480px;left:541px;display:flex;gap:14px}
.pager span{width:12px;height:12px;background:var(--dot)}
.pager span.active{background:var(--dot-active)}
.about-panel{left:131px;top:518px;width:939px;height:252px;
  background:repeating-linear-gradient(135deg,rgba(255,255,255,.25) 0 2px,transparent 2px 5px),linear-gradient(180deg,#e4e4e4,#f6f6f6 50%,#e2e2e2);
  box-shadow:0 10px 14px -8px rgba(0,0,0,.25)}
.stack{background:#fff;border:1px solid #d8d3c0;box-shadow:0 2px 6px rgba(0,0,0,.3)}
.stack-back{left:180px;top:552px;width:262px;height:186px;transform:rotate(-3deg)}
.stack-mid{left:186px;top:549px;width:262px;height:186px;transform:rotate(2deg)}
.stack-front{left:186px;top:550px;width:268px;height:190px;padding:6px;transform:rotate(2.5deg)}
.stack-front .photo{width:100%;height:100%}
h2{font-family:Oswald,sans-serif;font-weight:500;color:var(--blue);text-transform:uppercase;font-size:26px;line-height:32px;letter-spacing:-.2px}
p,li{font-size:11.3px;line-height:17px}
.about-title{left:480px;top:546px}
.about-copy{left:480px;top:588px;width:560px}
.features{left:480px;top:647px;list-style:none}
.features li{padding-left:16px;position:relative}
.features li::before{content:"";position:absolute;left:2px;top:8px;width:3px;height:3px;background:#777}
.btn{display:block;background:var(--button);color:var(--white);font-family:Oswald,sans-serif;font-size:13px;line-height:32px;text-align:center;text-decoration:none;border:1px solid #555;box-shadow:0 1px 2px rgba(0,0,0,.3)}
.btn-about{left:952px;top:712px;width:88px;height:33px}
.col-title-left{left:145px;top:809px}
.col-title-right{left:620px;top:809px}
.col-copy-left{left:145px;top:856px;width:270px}
.col-copy-right{left:621px;top:856px;width:278px}
.thumb{box-shadow:0 1px 3px rgba(0,0,0,.25)}
.thumb-suites{left:423px;top:858px;width:151px;height:84px;background:linear-gradient(180deg,#c9c7bd,#8b7a6a 55%,#5f7f3a)}
.thumb-barra{left:909px;top:858px;width:149px;height:93px;background:linear-gradient(180deg,#cfdbe6,#3d6f99 40%,#7d8e74 70%,#4b5b37)}
.btn-suites{left:147px;top:974px;width:88px;height:33px}
.site-footer{left:0;top:1041px;width:1200px;height:60px;background:linear-gradient(#151515,#0a0a0a)}
.footer-nav a{position:absolute;top:1063px;font-size:11.5px;line-height:14px;color:var(--footer-text);text-decoration:none;text-transform:uppercase}
.copyright{right:132px;top:1063px;font-size:11.5px;line-height:14px;color:var(--footer-text)}
</style>
</head>
<body>

<div class="abs hero-scene" role="img" aria-label="Aerial view of Barra da Tijuca with ocean, beach, lagoons and mountains"></div>

<header class="abs site-header">
  <div class="abs brand">SKYDECKRIO.COM</div>
  <nav class="abs main-nav">
    <a class="current" href="#" style="left:689px">Home</a>
    <a href="#" style="left:768px">Tranquil Cliff Suits</a>
    <a href="#" style="left:972px">The Apartment</a>
  </nav>
</header>

<div class="abs slide slide-side slide-left"><div class="photo" role="img" aria-label="Rooftop terrace with sun loungers beside the pool" style="background:linear-gradient(180deg,#3b4550 0%,#5a4b4b 45%,#d7d7d7 62%,#3aa6d8 85%,#7a4e36)"></div></div>
<div class="abs slide slide-side slide-right"><div class="photo" role="img" aria-label="Terrace barbecue area with brick grill and city view" style="background:linear-gradient(90deg,#b7926f 0%,#d3b08c 35%,#9cb6cc 55%,#6b3f35 80%,#3a3d35)"></div></div>
<div class="abs slide slide-main"><div class="photo" role="img" aria-label="Living room with sofa, glass coffee table, orchids and colourful paintings" style="background:linear-gradient(180deg,#d9d6cf 0%,#e6e2da 35%,#8b7765 60%,#5a2e1c 85%,#3d1e12)"></div></div>

<div class="abs pager"><span class="active"></span><span></span><span></span><span></span><span></span></div>

<section class="abs about-panel"></section>
<div class="abs stack stack-back"></div>
<div class="abs stack stack-mid"></div>
<div class="abs stack stack-front"><div class="photo" role="img" aria-label="Pool deck with loungers under a white awning" style="background:linear-gradient(180deg,#eaeaea 0%,#3e4650 25%,#6a4a48 50%,#d4d4d4 65%,#2fa3d6 82%,#7b4b33)"></div></div>

<h2 class="abs about-title">About the Apartment</h2>
<p class="abs about-copy">Aenean diam eros, tempor in congue vel, interdum sit amet eros. Mauris interdum, sapien non aliquam aliquam, enim nulla rutrum nisl, quis mattis odio diam vitae nibh. Etiam nec dolor nec leo aliquam consequat nec eu felis. Phasellus interdum facilisis nisi.</p>
<ul class="abs features">
  <li>251 m2 Duplex Penthouse</li>
  <li>4 suites</li>
  <li>maids room with bath</li>
  <li>guest bathroom</li>
  <li>living room</li>
</ul>
<a class="abs btn btn-about" href="#">View More</a>

<h2 class="abs col-title-left">Tranquil Cliff Suites</h2>
<p class="abs col-copy-left">Aenean diam eros, tempor in congue vel, interdum sit amet eros. Mauris interdum, sapien non aliquam aliquam, Mauris interdum, sapien non aliquam aliquam, enim nulla rutrum nisl, quis mattis odio diam vitae nibh.enim nulla rutrum nisl, quis mattis odio diam vitae nibh.</p>
<div class="abs thumb thumb-suites" role="img" aria-label="Condominium entrance canopy surrounded by greenery"></div>
<a class="abs btn btn-suites" href="#">View More</a>

<h2 class="abs col-title-right">Barra da Tijuca</h2>
<p class="abs col-copy-right">Aenean diam eros, tempor in congue vel, interdum sit amet eros. Mauris interdum, sapien non aliquam aliquam, Mauris interdum, sapien non aliquam aliquam,&nbsp; quis mattis odio diam vitae nibh.enim nulla rutrum nisl, quis mattis odio diam vitae nibh.enim nulla rutrum nisl, quis mattis odio diam vitae nibh.enim nulla rutrum nisl, quis mattis odio diam vitae nibh quis mattis odio diam vitae nibh.enim nulla rutrum nisl.</p>
<div class="abs thumb thumb-barra" role="img" aria-label="Aerial view of Barra da Tijuca beach and coastline"></div>

<footer class="abs site-footer"></footer>
<nav class="footer-nav">
  <a href="#" style="left:133px">Home</a>
  <a href="#" style="left:198px">Tranquil Cliff Suits</a>
  <a href="#" style="left:387px">The Apartment</a>
</nav>
<div class="abs copyright">Copyright © 2013&nbsp; All Rights Reserved.</div>

</body>
</html>
```